Ward Compass Business Card Design*

We need a business card design for our company Ward Compass. Our company is specialized in providing online consulting services regarding medical institutions, hospitals and doctors. We work with patients worldwide looking to choose between healthcare providers. We have a website you may use as a reference, where we list doctors and clinics worldwide. So we target Medical providers as well as patients worldwide.
Target Market(s)
Medical Providers and patients around the world
Industry/Entity Type
Medical
Contact Information for Business Card
Salwa Kettani
CEO
+90 612 348 2175
info@wardcompass.example
www.wardcompass.example
14 Annakhil 7 H.R.B. Rabat, Morocco
Requirements
Must have
- Company logo/name on one full side, personal info and smaller logo and company name on the other side.
Nice to have
- Smart and elegant design

```html
<!DOCTYPE html>
<html lang="en">
<head>
<meta charset="utf-8">
<title>Ward Compass — Business Card</title>
<link href="https://fonts.googleapis.com/css2?family=Montserrat:wght@600&family=Roboto:wght@400;500;700&display=swap" rel="stylesheet">
<style>
  :root {
    --navy: #143966;
    --white: #ffffff;
    --backdrop: #d6d5d2;
    --line: rgba(255,255,255,0.8);
  }
  * { box-sizing: border-box; margin: 0; padding: 0; }
  html, body {
    width: 1200px; height: 801px; overflow: hidden;
    background: var(--backdrop);
  }
  .sheet {
    position: relative; width: 1200px; height: 801px;
    display: flex; align-items: center; justify-content: center; gap: 60px;
  }
  .card {
    position: relative; width: 520px; height: 297px; overflow: hidden;
    background: var(--navy);
    box-shadow: 0 10px 28px rgba(0,0,0,0.22);
  }
  /* Front */
  .front-split { position: absolute; inset: 0; width: 520px; height: 297px; }
  .brand-name {
    position: absolute; right: 266px; top: 98px;
    font-family: "Montserrat", sans-serif; font-weight: 600;
    font-size: 25px; letter-spacing: 0.4px; color: var(--navy);
    white-space: nowrap; line-height: 1;
  }
  .brand-dot {
    position: absolute; left: 252px; top: 85px; width: 96px; height: 96px;
    border-radius: 50%; background: var(--navy); border: 5px solid var(--white);
  }
  .person {
    position: absolute; right: 192px; top: 190px; text-align: right;
    font-family: "Roboto", sans-serif; color: var(--white); line-height: 1.25;
  }
  .person-name { font-weight: 700; font-size: 14px; letter-spacing: 0.6px; }
  .person-role { font-weight: 500; font-size: 13px; letter-spacing: 0.5px; }
  .divider {
    position: absolute; left: 340px; top: 186px; width: 1px; height: 46px;
    background: var(--line);
  }
  .contacts {
    position: absolute; left: 356px; top: 150px; list-style: none;
    font-family: "Roboto", sans-serif; font-size: 11px; color: var(--white);
  }
  .contacts li { display: flex; align-items: center; gap: 6px; height: 19px; white-space: nowrap; }
  .contacts svg { width: 9px; height: 9px; fill: var(--white); flex: none; }
  .address {
    position: absolute; left: 178px; top: 248px;
    font-family: "Roboto", sans-serif; font-size: 12px; color: var(--white);
    letter-spacing: 0.2px; white-space: nowrap;
  }
  /* Back */
  .back-field { position: absolute; inset: 0; background: var(--navy); }
  .back-mark {
    position: absolute; right: 40px; top: 50%; transform: translateY(-50%);
    display: flex; align-items: center; gap: 10px;
  }
  .back-dot { width: 22px; height: 22px; border-radius: 50%; background: var(--white); }
  .back-name {
    font-family: "Montserrat", sans-serif; font-weight: 600; font-size: 20px;
    color: var(--white); letter-spacing: 0.5px; white-space: nowrap;
  }
</style>
</head>
<body>
<main class="sheet">
  <section class="card card--front" aria-label="Business card front">
    <svg class="front-split" viewBox="0 0 520 297" aria-hidden="true">
      <polygon points="0,0 520,0 520,120 0,148" fill="#ffffff"/>
    </svg>
    <div class="brand-name">WARD COMPASS</div>
    <div class="brand-dot"></div>
    <div class="person">
      <div class="person-name">SALWA KETTANI</div>
      <div class="person-role">CEO</div>
    </div>
    <div class="divider"></div>
    <ul class="contacts">
      <li><svg viewBox="0 0 10 10"><path d="M2 0.5l2 2-1 1.2c.6 1.3 1.6 2.3 2.9 2.9l1.2-1 2 2-1.3 1.9C4.3 9.2.8 5.7.3 1.8z"/></svg>+90 612 348 2175</li>
      <li><svg viewBox="0 0 10 10"><path d="M0 2h10v6H0zM1 3l4 2.8L9 3v-.1H1z" fill-rule="evenodd"/></svg>info@wardcompass.example</li>
      <li><svg viewBox="0 0 10 10"><circle cx="5" cy="5" r="4.5"/></svg>www.wardcompass.example</li>
    </ul>
    <div class="address">14 Annakhil 7 H.R.B.Rabat, Morocco</div>
  </section>

  <section class="card card--back" aria-label="Business card back">
    <div class="back-field" role="img" aria-label="Navy background with a faint repeating brand-mark pattern"></div>
    <div class="back-mark">
      <span class="back-dot"></span>
      <span class="back-name">WARD COMPASS</span>
    </div>
  </section>
</main>
</body>
</html>
```